Bold, Modern, Clean "Kestrelwaymassage.com" website

Why we stand out?
We are a male and female mobile massage team. Our names are Paul and Lina. 
Kestrel Way is a Seattle based mobile massage service. Our massage is offered to the community with a goal of facilitating balance within each individual. We specialize in integrated Pain management, and sports/medical massage therapy. Every client's first assessment is attended by our male and female massage therapist team. Depending on the goals identified for an individual determines which therapist will be assigned to provide treatment, if not both.

Our passion...
Here at Kestrel Way, we have a great passion for Postural Resoration and how it is integrated into an individual's Massage treatment. We pride ourselves in being natural facilitators of healing, which takes the ego of the therapist out of the client's healing process. We strive to deliver the best massage possible by including modalities such as Neuromuscular, Myofascial release, spontaneous muscle release, postural restoration, orthopedic, and medical massage.

Our education...

We are both Graduates of Venmora, school of massage therapy. We have continuing education in medical massage, myofacial release, trigger point therapy, postural restoration, anatomy, and spontaneous muscle release. Lina is also a Certified Yoga Instructor, which amplifies her experience with flexibility and strength as it pertains to each individual. Paul's passion is Massage, stretching, and strength training to encourage postural restoration and realignment.

Our rates-

Our rates are $75/ 60 minutes, $95/ 90 minutes, and $120/ 120 minutes.

Education-
Both Lina and I worked as behavioral health professionals that specialized in life skills mentoring for youth who had experienced different types of trauma. This led us both to want to help others in a different environment, where individuals can be empowered to take responsibility over their own healing. To us, massage is a type of manipulation physical therapy, that encourages healing on many levels.

Advice to any massage client-
The most important thing to 'us', as Licenced providers is to get you on to our table to show you our skills. But a good therapist never forgets that it's not about what we do for you, but what we can facilitate for you. Your health and healing has nothing to do with us. It is yours, not ours. Identify what your goals are with any Therapist, and know what the end looks like. Progress should be tangible, such as range of motion, and decreased pain.

Lina and Paul at Kestrel Way are awesome! I recently had open heart surgery, and Lina worked on me to increase my range of motion while helping with the pinched nerve from my arm being in the same position for so long during my surgery. My wife drives a lot for work, and Paul has helped decrease her neck and lower back pain immensely. They are seriously the best therapists I have ever worked with. I would recommend them to anyone who needs anything from stress relief to a medical massage treatment. They are professional, up beat, easy going, and always on time. And, I love that they meet us where ever we like! We did a staycation recently, where they came to our hotel to give us relaxation massages. Although usually they come to our home, where we focus on pain related issues. We will continue to work with them for a long, long time.

Target Market(s)

Mobile massage therapy clients

Industry/Entity Type

Massage Therapy

Coding

Coded - Design and coding required

Number of Pages Required

1 page

Font styles to use
Serif
Sans Serif

Requirements
Must have
• Please add or remove any information that would help the presentation of our website. Our logo is posted below, please include into the website.
• Please include a contact field that includes, kestrelwaymassage@fernmail.net,
• (206) 555-0148
• We have also included our own stock photos, as well as a photo of Paul and Lina. Please include a cropped photo of both massage therapists.

```html
<!DOCTYPE html>
<html lang="en">
<head>
<meta charset="utf-8">
<title>Kestrel Way Mobile Massage</title>
<link rel="stylesheet" href="https://fonts.googleapis.com/css2?family=Lato:ital,wght@0,400;0,700;0,900;1,400&display=swap">
<style>
:root{
  --teal:#19c6c9;
  --teal-dark:#0fa7ab;
  --blue:#2a3fc0;
  --blue-deep:#1b2a9a;
  --ink:#222;
  --body:#3a3a3a;
  --muted:#666;
  --white:#fff;
  --footer:#1d1d1d;
  --submit:#1a1a1a;
  --overlay:rgba(40,40,40,.72);
}
*{box-sizing:border-box;margin:0;padding:0}
html,body{width:1200px;height:2903px;overflow:hidden}
body{font-family:"Lato",Arial,sans-serif;color:var(--body);background:var(--white);position:relative}
.abs{position:absolute}

/* header */
.topbar{top:0;left:0;width:1200px;height:80px;background:var(--white)}
.contact{top:24px;display:flex;align-items:center;gap:12px;font-size:19px;color:var(--blue);font-weight:700}
.contact.phone{left:84px}
.contact.mail{right:84px;font-weight:400;font-size:17px}
.icon-circle{width:32px;height:32px;border:2px solid var(--blue);border-radius:50%;display:flex;align-items:center;justify-content:center}
.navband{top:80px;left:0;width:1200px;height:44px;background:linear-gradient(var(--teal),var(--teal-dark));z-index:3}
.navband a{position:absolute;top:11px;font-size:17px;font-weight:700;color:var(--white);text-decoration:none;white-space:nowrap}
.brand{top:13px;left:513px;width:174px;height:174px;border-radius:50%;background:var(--white);border:4px solid var(--blue);z-index:4;display:flex;flex-direction:column;align-items:center;justify-content:center;text-align:center;color:var(--blue);font-weight:900}
.brand .name{font-size:30px;line-height:1.05}
.brand .tag{font-size:14px;font-weight:700;margin-top:6px}

/* hero */
.hero{top:124px;left:0;width:1200px;height:580px;background:linear-gradient(160deg,#a9c3da 0%,#d9e4ee 35%,#e9cdb8 60%,#c99b80 80%,#eee 100%)}
.hero-caption{top:491px;left:0;width:1200px;height:89px;background:var(--overlay);color:var(--white);font-weight:700;font-size:27px;line-height:35px;text-align:center;padding-top:9px}
.arrow{top:250px}

/* sections */
.section-title{font-size:33px;font-weight:400;text-align:center;color:var(--ink);width:1200px;left:0}
.divider{left:325px}
.copy{left:110px;width:980px;text-align:center;font-size:15px;line-height:26.5px}
.band{left:0;width:1200px}
.band.passion{top:987px;height:315px;background:linear-gradient(100deg,#6e6e6e,#8d8884 45%,#b4aca6 75%,#8d8986)}
.band.advice{top:1809px;height:319px;background:linear-gradient(100deg,#575757,#7c7875 40%,#8f8c88 70%,#6a6866)}
.band::after{content:"";position:absolute;inset:0;background:rgba(30,30,30,.45)}
.light{color:var(--white);z-index:2}

/* cards */
.card{top:1358px;width:317px;height:397px;border:1px solid #d6d6d6;border-top:3px solid var(--teal);border-bottom:3px solid var(--blue);background:var(--white);padding:16px 18px}
.card h3{font-size:32px;font-weight:700;color:var(--teal);line-height:36px}
.card h3 span{color:var(--blue)}
.card .photo{margin-top:12px;width:281px;height:122px;border:1px solid #ccc}
.card p{margin-top:14px;font-size:13.5px;line-height:19.5px;text-align:justify;letter-spacing:.2px}
.rates{list-style:none;margin-top:6px}
.rates li{font-size:19px;line-height:32px;display:flex;align-items:center;gap:10px;color:var(--ink)}

/* reviews */
.quote{left:110px;width:980px;text-align:center;font-style:italic;font-size:14px;line-height:27px;color:var(--body)}
.qmark{font-size:70px;color:#c9c9c9;font-family:Georgia,serif;line-height:1}
.review-meta{top:2455px;left:0;width:1200px;text-align:center;font-size:14px;font-style:italic;color:var(--blue)}
.badge{top:2496px;left:556px;width:88px;height:26px;background:#e3b23c;border-radius:3px}

/* inquiry */
.inquiry{top:2573px;left:0;width:1200px;height:225px;background:var(--blue)}
.field{top:140px;height:46px;background:var(--white);font-size:14px;color:#888;padding:14px 12px}
.submit{top:140px;left:913px;width:201px;height:46px;background:var(--submit);color:var(--white);font-weight:700;font-size:20px;text-align:center;line-height:46px}

/* footer */
.footer{top:2798px;left:0;width:1200px;height:105px;background:var(--footer);color:var(--white);text-align:center}
.footer nav{margin-top:24px;font-size:15px}
.footer nav span.sep{color:#888;margin:0 10px}
.footer .copyright{margin-top:16px;font-size:14px;color:#ddd}
</style>
</head>
<body>

<header>
  <div class="abs topbar"></div>
  <div class="abs contact phone">
    <span class="icon-circle"><svg width="16" height="16" viewBox="0 0 24 24"><path fill="#2a3fc0" d="M6.6 10.8a15.1 15.1 0 0 0 6.6 6.6l2.2-2.2c.3-.3.7-.4 1-.2 1.1.4 2.3.6 3.6.6.6 0 1 .4 1 1V20c0 .6-.4 1-1 1A17 17 0 0 1 3 4c0-.6.4-1 1-1h3.5c.6 0 1 .4 1 1 0 1.3.2 2.5.6 3.6.1.3 0 .7-.2 1z"/></svg></span>
    (206) 555-0148
  </div>
  <div class="abs contact mail">
    <span class="icon-circle"><svg width="16" height="12" viewBox="0 0 16 12"><rect x="0.5" y="0.5" width="15" height="11" fill="#2a3fc0"/><path d="M1 1l7 6 7-6" stroke="#fff" stroke-width="1.4" fill="none"/></svg></span>
    kestrelwaymassage@fernmail.net
  </div>
  <nav class="abs navband">
    <a href="#why" style="left:87px">Why We Stand Out?</a>
    <a href="#passion" style="left:282px">Our Passion</a>
    <a href="#education" style="left:416px">Education</a>
    <a href="#rates" style="left:712px">Rates</a>
    <a href="#advice" style="left:786px">Advice To Any Massage Client</a>
    <a href="#reviews" style="left:1049px">Reviews</a>
  </nav>
  <div class="abs brand"><span class="name">KESTREL<br>WAY</span><span class="tag">mobile massage</span></div>
</header>

<section class="abs hero" role="img" aria-label="Therapist treating a client's knee during a sports massage session">
  <svg class="abs arrow" style="left:38px" width="28" height="52" viewBox="0 0 28 52"><path d="M25 2L3 26l22 24" stroke="#fff" stroke-width="2" fill="none"/></svg>
  <svg class="abs arrow" style="right:38px" width="28" height="52" viewBox="0 0 28 52"><path d="M3 2l22 24L3 50" stroke="#fff" stroke-width="2" fill="none"/></svg>
  <div class="abs hero-caption">We Are A Seattle Based Mobile Massage Service Specialize In Integrated Pain<br>Management, And Sports/medical Massage Therapy.</div>
</section>

<section id="why">
  <h2 class="abs section-title" style="top:743px">Why We Stand Out?</h2>
  <svg class="abs divider" style="top:799px" width="550" height="20" viewBox="0 0 550 20"><line x1="0" y1="10" x2="250" y2="10" stroke="#19c6c9"/><line x1="300" y1="10" x2="550" y2="10" stroke="#19c6c9"/><circle cx="254" cy="10" r="5" fill="none" stroke="#19c6c9" stroke-width="1.5"/><circle cx="275" cy="10" r="7" fill="none" stroke="#19c6c9" stroke-width="1.5"/><circle cx="275" cy="10" r="4" fill="#2a3fc0"/><circle cx="296" cy="10" r="5" fill="none" stroke="#19c6c9" stroke-width="1.5"/></svg>
  <p class="abs copy" style="top:838px">We are a male and female mobile massage team. Our names are Paul and Lina. Kestrel Way is a Seattle based mobile massage service. Our massage is offered to the community with a goal of facilitating balance within each individual. We specialize in integrated Pain management, and sports/medical massage therapy. Every client's first assessment is attended by our male and female massage therapist team. Depending on the goals identified for an individual determines which therapist will be assigned to provide treatment, if not both.</p>
</section>

<section id="passion" class="abs band passion" role="img" aria-label="Client relaxing during a back massage, softened backdrop">
  <h2 class="abs section-title light" style="top:58px;color:#fff">Our Passion</h2>
  <svg class="abs divider light" style="top:103px" width="550" height="20" viewBox="0 0 550 20"><line x1="0" y1="10" x2="250" y2="10" stroke="#fff" stroke-opacity=".7"/><line x1="300" y1="10" x2="550" y2="10" stroke="#fff" stroke-opacity=".7"/><circle cx="254" cy="10" r="5" fill="none" stroke="#fff" stroke-width="1.5"/><circle cx="275" cy="10" r="7" fill="none" stroke="#fff" stroke-width="1.5"/><circle cx="275" cy="10" r="4" fill="#fff"/><circle cx="296" cy="10" r="5" fill="none" stroke="#fff" stroke-width="1.5"/></svg>
  <p class="abs copy light" style="top:163px;font-weight:700">We are both Graduates of Venmora, school of massage therapy. We have continuing education in medical massage, myofacial release, trigger point therapy, postural restoration, anatomy, and spontaneous muscle release. Lina is also a Certified Yoga Instructor, which amplifies her experience with flexibility and strength as it pertains to each individual. Paul's passion is Massage, stretching, and strength training to encourage postural restoration and realignment.</p>
</section>

<section id="education">
  <article class="abs card" style="left:85px">
    <h3>About <span>Paul</span></h3>
    <div class="photo" role="img" aria-label="Portrait of Paul in the treatment room" style="background:linear-gradient(90deg,#e6e3df,#d3c3b6 55%,#eee)"></div>
    <p>Paul Graduate of Venmora, school of massage therapy, ontinuing education in medical massage, myofacial release, trigger point therapy, postural restoration, anatomy, and spontaneous muscle releasePaul's passion is Massage, stretching, and strength training to encourage postural restoration and realignment.</p>
  </article>
  <article class="abs card" style="left:441px">
    <h3>About <span>Lina</span></h3>
    <div class="photo" role="img" aria-label="Portrait of Lina" style="background:linear-gradient(90deg,#e9e9e9,#e7cdb7 50%,#ececec)"></div>
    <p>Lina is also a Certified Yoga Instructor, which amplifies her experience with flexibility and strength as it pertains to each individual. I worked as behavioral health professionals that specialized in life skills mentoring for youth who had experienced different types of trauma and massage is a type of manipulation physical therapy, that encourages healing on many levels.</p>
  </article>
  <article id="rates" class="abs card" style="left:797px">
    <h3>Our <span>Rates</span></h3>
    <div class="photo" role="img" aria-label="Spa stones with an orchid" style="background:linear-gradient(90deg,#c9e6f2,#e9f3f6 45%,#7a8a5a 75%,#c58bc2)"></div>
    <p style="text-align:left;font-size:14px">Lorem ipsum dolor sit amet, consectetuer adipiscing elit, sed diam nonummy nibh euismod tincidunt ut laoreet dolore magna aliquam erat volutpat.</p>
    <ul class="rates">
      <li><svg width="18" height="16" viewBox="0 0 18 16"><path d="M2 8l5 5L16 2" stroke="#0fa7ab" stroke-width="3" fill="none"/></svg>$75/ 60 minutes</li>
      <li><svg width="18" height="16" viewBox="0 0 18 16"><path d="M2 8l5 5L16 2" stroke="#0fa7ab" stroke-width="3" fill="none"/></svg>$95/ 90 minutes</li>
      <li><svg width="18" height="16" viewBox="0 0 18 16"><path d="M2 8l5 5L16 2" stroke="#0fa7ab" stroke-width="3" fill="none"/></svg>$120/ 120 minutes</li>
    </ul>
  </article>
</section>

<section id="advice" class="abs band advice" role="img" aria-label="Therapist massaging a client's back, softened backdrop">
  <h2 class="abs section-title light" style="top:62px;color:#fff">Advice To Any Massage Client</h2>
  <svg class="abs divider light" style="top:107px" width="550" height="20" viewBox="0 0 550 20"><line x1="0" y1="10" x2="250" y2="10" stroke="#fff" stroke-opacity=".7"/><line x1="300" y1="10" x2="550" y2="10" stroke="#fff" stroke-opacity=".7"/><circle cx="254" cy="10" r="5" fill="none" stroke="#fff" stroke-width="1.5"/><circle cx="275" cy="10" r="7" fill="none" stroke="#fff" stroke-width="1.5"/><circle cx="275" cy="10" r="4" fill="#fff"/><circle cx="296" cy="10" r="5" fill="none" stroke="#fff" stroke-width="1.5"/></svg>
  <p class="abs copy light" style="top:162px;left:100px;width:1000px;font-size:17px;line-height:26px">The most important thing to 'us', as Licenced providers is to get you on to our table to show you our skills. But a good therapist never forgets that it's not about what we do for you, but what we can facilitate for you. Your health and healing has nothing to do with us. It is yours, not ours. Identify what your goals are with any Therapist, and know what the end looks like. Progress should be tangible, such as range of motion, and decreased pain.</p>
</section>

<section id="reviews">
  <h2 class="abs section-title" style="top:2179px">Client Reviews</h2>
  <svg class="abs divider" style="top:2235px" width="550" height="20" viewBox="0 0 550 20"><line x1="0" y1="10" x2="250" y2="10" stroke="#19c6c9"/><line x1="300" y1="10" x2="550" y2="10" stroke="#19c6c9"/><circle cx="254" cy="10" r="5" fill="none" stroke="#19c6c9" stroke-width="1.5"/><circle cx="275" cy="10" r="7" fill="none" stroke="#19c6c9" stroke-width="1.5"/><circle cx="275" cy="10" r="4" fill="#2a3fc0"/><circle cx="296" cy="10" r="5" fill="none" stroke="#19c6c9" stroke-width="1.5"/></svg>
  <span class="abs qmark" style="top:2270px;left:82px">&ldquo;</span>
  <span class="abs qmark" style="top:2392px;left:1092px">&rdquo;</span>
  <svg class="abs" style="top:2316px;left:36px" width="14" height="26" viewBox="0 0 14 26"><path d="M12 2L2 13l10 11" stroke="#bbb" stroke-width="2" fill="none"/></svg>
  <svg class="abs" style="top:2316px;right:36px" width="14" height="26" viewBox="0 0 14 26"><path d="M2 2l10 11L2 24" stroke="#bbb" stroke-width="2" fill="none"/></svg>
  <p class="abs quote" style="top:2284px">Lina and Paul at Kestrel Way are awesome! I recently had open heart surgery, and Lina worked on me to increase my range of motion while helping with the pinched nerve from my arm being in the same position for so long during my surgery. My wife drives a lot for work, and Paul has helped decrease her neck and lower back pain immensely. They are seriously the best therapists I have ever worked with. I would recommend them to anyone who needs anything from stress relief to a medical massage treatment. They are professional, upbeat, easy going, and always on time. And, I love that they meet us where ever we like! We did a staycation recently, where they came to our hotel to give us relaxation massages. Although usually they come to our home, where we focus on pain related issues. We will continue to work with them for a long, long time.</p>
  <p class="abs review-meta">5/5 stars Massage Therapy Verified Review</p>
  <div class="abs badge" aria-hidden="true"></div>
</section>

<section class="abs inquiry">
  <h2 class="abs section-title" style="top:30px;color:#fff">Quick Inquiry</h2>
  <svg class="abs divider" style="top:85px" width="550" height="20" viewBox="0 0 550 20"><line x1="0" y1="10" x2="250" y2="10" stroke="#fff" stroke-opacity=".7"/><line x1="300" y1="10" x2="550" y2="10" stroke="#fff" stroke-opacity=".7"/><circle cx="254" cy="10" r="5" fill="none" stroke="#fff" stroke-width="1.5"/><circle cx="275" cy="10" r="7" fill="none" stroke="#fff" stroke-width="1.5"/><circle cx="275" cy="10" r="4" fill="#fff"/><circle cx="296" cy="10" r="5" fill="none" stroke="#fff" stroke-width="1.5"/></svg>
  <div class="abs field" style="left:85px;width:205px">Name</div>
  <div class="abs field" style="left:313px;width:206px">Email</div>
  <div class="abs field" style="left:538px;width:358px">Message</div>
  <div class="abs submit">Submit</div>
</section>

<footer class="abs footer">
  <nav>Why We Stand Out?<span class="sep">&bull;</span>Our Passion<span class="sep">&bull;</span>Education<span class="sep">&bull;</span>Rates<span class="sep">&bull;</span>Advice To Any Massage Client<span class="sep">&bull;</span>Reviews</nav>
  <p class="copyright">&copy; 2015 Kestrel Way Mobile Massage. All Rights Reserved.</p>
</footer>

</body>
</html>
```